Website for IT consulting Company

I need a website upgrade, the existing site content is ok, I would also like to add a testimonial page, the site should be something that is easy for us to update content. You use the content from www.kelvanbrook.com as an example. I will also post update logo and artwork. I also need a contact form with some type of validation or captcha.

I added Coded to the Project

Please omit Address maps

Target Market(s)

small business, service oriented companies. We provide IT Consulting, support and mangement

Industry/Entity Type

Information Technology

Coding

Number of Pages Required

1 page

Font styles to use
Serif
Sans Serif

Requirements
Must have
• Contain logo attached, and content from existing web site www.kelvanbrook.com.
• Also need to update content easily, and be movable to different platforms.
• There is a catch phrase
• "Let us worry about your technology…” “ so you don’t have to!”
• Should be included.
Nice to have
• Testimonial page, Project page where we can post new and past projects and pictures
Should not have
• none

```html
<!DOCTYPE html>
<html lang="en">
<head>
<meta charset="utf-8">
<title>Kelvanbrook – IT Solutions</title>
<link rel="stylesheet" href="https://fonts.googleapis.com/css2?family=Cinzel:wght@700&family=Lato:wght@400;700&family=Questrial&display=swap">
<style>
:root{
  --orange:#f29a2e;
  --orange-deep:#d97a10;
  --black:#050505;
  --charcoal:#3d3d3f;
  --band-grey:#67686b;
  --text:#333;
  --muted:#9a9a9a;
  --line:#cfcfcf;
  --white:#fff;
}
*{box-sizing:border-box;margin:0;padding:0}
html,body{width:1200px;height:2507px;overflow:hidden}
body{position:relative;background:var(--white);font-family:"Lato",sans-serif;color:var(--text)}
.abs{position:absolute}

/* header */
.topbar{left:0;top:0;width:1200px;height:105px;background:var(--black)}
.brand{display:flex;align-items:center;gap:12px;font-family:"Questrial",sans-serif;color:#d6d6d6;font-size:40px;letter-spacing:1px}
.brand-square{width:34px;height:34px;background:var(--orange);border-radius:4px}
.topbar .brand{position:absolute;left:99px;top:30px}
.social-top{left:838px;top:22px;display:flex;gap:6px}
.social-top span{width:20px;height:20px;background:#8a6a3a;border-radius:3px}
.phone{left:927px;top:38px;display:flex;align-items:center;gap:20px;color:var(--white);font-size:20px}
.phone-icon{width:28px;height:28px;background:#e8e8e8;border-radius:4px;display:flex;align-items:center;justify-content:center}

.mainnav{left:0;top:105px;width:1200px;height:45px;background:linear-gradient(#f7a640,#ec8c1c)}
.mainnav a{position:absolute;top:0;height:45px;line-height:45px;color:var(--white);font-weight:700;font-size:17px;text-decoration:none;letter-spacing:.5px}
.mainnav a.active{background:#2c2c2c;padding:0 8px;margin-left:-8px}

/* hero */
.hero{left:0;top:150px;width:1200px;height:535px;background:linear-gradient(100deg,#e9e6e1 0%,#cfc8bf 35%,#7b7f86 65%,#3d4a5d 100%)}
.hero-tag{left:100px;top:236px;font-family:"Cinzel",serif;font-weight:700}
.hero-tag .l1{font-size:26px;color:#111;letter-spacing:.5px}
.hero-tag .l2{font-size:29px;color:var(--orange);margin-top:6px}
.hero-next{left:1124px;top:345px}

/* welcome */
.welcome{left:0;top:705px;width:1200px;text-align:center;font-family:"Questrial",sans-serif;font-size:36px;color:#555}
.welcome b{font-weight:400;color:#777}
.divider{height:2px;background:var(--line)}
.divider-mark{width:16px;height:16px;background:var(--orange);border-radius:3px}
.intro{left:100px;top:806px;width:1000px;text-align:center;font-family:"Questrial",sans-serif;font-size:21px;line-height:34px;color:#333}

/* services */
.service-band{left:0;top:1111px;width:1200px;height:209px;background:var(--band-grey)}
.card{top:916px;width:316px;height:246px;border:4px solid var(--orange);overflow:hidden}
.card .photo{width:100%;height:100%}
.card .badge{position:absolute;left:50%;bottom:-47px;transform:translateX(-50%);width:94px;height:94px;border-radius:50%;background:var(--orange)}
.card .badge i{position:absolute;left:35px;top:16px;width:24px;height:22px;border:3px solid var(--white);border-radius:4px}
.service-title{top:1184px;width:316px;text-align:center;color:var(--white);font-weight:700;font-size:19px}
.readmore{top:1241px;display:flex;align-items:center}
.readmore span{display:inline-block;background:var(--orange);color:var(--white);font-size:13px;padding:6px 12px;border:2px solid #f5c48a;border-radius:4px;letter-spacing:.5px}
.readmore i{width:24px;height:24px;background:var(--orange);border:2px solid #f5c48a;border-radius:4px;margin-left:-4px}

/* mission / vision */
.mission{left:0;top:1320px;width:600px;height:256px;background:var(--orange)}
.vision{left:600px;top:1320px;width:600px;height:256px;background:var(--orange-deep)}
.mv h2{font-family:"Lato",sans-serif;font-weight:400;font-size:30px;color:var(--white);padding-bottom:8px;border-bottom:1px solid rgba(255,255,255,.5);display:inline-block;min-width:200px}
.mv p{font-size:15.5px;line-height:25px;color:var(--white);margin-top:14px}
.mv p em{font-style:normal;color:#f7c37a}
.mission-text{left:126px;top:1362px;width:350px;text-align:right}
.vision-text{left:735px;top:1362px;width:330px}
.mv-circle{left:520px;top:1367px;width:160px;height:160px;border-radius:50%;background:var(--white);border:8px solid #f7b564;display:flex;align-items:center;justify-content:center}
.mv-circle i{width:54px;height:54px;background:var(--orange);border-radius:8px}

/* testimonials */
.testi-title{left:0;top:1604px;width:1200px;text-align:center;font-family:"Questrial",sans-serif;font-size:36px;color:#111}
.testi-title span{color:var(--orange)}
.avatar{top:1739px;width:84px;height:84px;border-radius:50%;border:4px solid #8d8d8d;background:radial-gradient(circle at 50% 40%,#d8cfc6,#8e8a86)}
.avatar.featured{border-color:var(--orange)}
.person{top:1838px;width:316px;text-align:center}
.person .name{font-size:14px;color:#222}
.person .handle{font-size:13px;font-weight:700;color:#b9b9b9;margin-top:8px}
.person .handle.featured{color:var(--orange)}
.quote{top:1905px;width:316px;height:126px;border:1px solid #ddd;background:var(--white);padding:20px 18px 0 20px;box-shadow:0 2px 3px rgba(0,0,0,.06)}
.quote.featured{border-bottom:3px solid var(--orange)}
.quote p{font-size:13.5px;line-height:22px;color:#333}
.quote p b{color:#bbb;font-size:22px;line-height:0;margin-right:6px}
.quote time{display:block;font-size:12px;color:#999;margin-top:10px}

/* footer */
.footer-curve{left:0;top:2100px}
.footer-mark{left:570px;top:2088px;width:60px;height:60px;background:var(--orange);border-radius:10px;border:4px solid var(--white)}
.fcol h3{font-family:"Questrial",sans-serif;font-weight:400;font-size:23px;color:var(--white);padding-bottom:10px;border-bottom:1px solid #5a5a5c}
.fcol h3 span{color:var(--orange)}
.links{left:100px;top:2222px;width:200px}
.links ul{list-style:none;margin-top:14px}
.links li{font-size:13.5px;color:#e5e5e5;height:24px;padding-left:14px;position:relative}
.links li::before{content:"";position:absolute;left:0;top:6px;width:5px;height:5px;border-radius:50%;background:var(--orange)}
.contact-detail{left:341px;top:2222px;width:220px;font-size:13.5px;color:#e5e5e5}
.contact-detail p{line-height:22px}
.contact-detail .row{display:flex;align-items:center;gap:10px;margin-top:14px;font-size:13px}
.contact-detail .row i{width:12px;height:12px;background:var(--orange);border-radius:2px}
.quick-contact{left:603px;top:2222px;width:282px}
.field{width:258px;height:34px;background:var(--white);border:1px solid #ccc;font-size:12px;color:#777;padding:9px 10px;margin-top:8px}
.field:first-of-type{margin-top:16px}
.submit{width:120px;height:32px;background:var(--orange);color:var(--white);font-size:14px;text-align:center;line-height:32px;margin-top:8px}
.vsep{width:1px;height:210px;background:#555}
.footer-brand{left:916px;top:2270px}
.footer-brand .brand{font-size:30px;gap:8px}
.footer-brand .brand-square{width:24px;height:24px}
.social-foot{left:950px;top:2362px;display:flex;gap:16px}
.social-foot span{width:28px;height:28px;border-radius:3px;background:#1f88c9}
.copybar{left:0;top:2465px;width:1200px;height:42px;background:var(--orange);color:var(--white);font-size:13px;text-align:center;line-height:42px}
</style>
</head>
<body>

<header class="abs topbar">
  <div class="brand"><span class="brand-square"></span>KELVANBROOK</div>
</header>
<div class="abs social-top" aria-label="Social links"><span></span><span></span><span></span></div>
<div class="abs phone">
  <span class="phone-icon"><svg width="16" height="16" viewBox="0 0 24 24"><path d="M6.6 10.8a15 15 0 0 0 6.6 6.6l2.2-2.2a1 1 0 0 1 1-.25 11.4 11.4 0 0 0 3.6.6 1 1 0 0 1 1 1V20a1 1 0 0 1-1 1A17 17 0 0 1 3 4a1 1 0 0 1 1-1h3.5a1 1 0 0 1 1 1c0 1.25.2 2.45.6 3.6a1 1 0 0 1-.25 1z" fill="#111"/></svg></span>
  (555) 014-2290
</div>

<nav class="abs mainnav">
  <a class="active" style="left:152px">HOME</a>
  <a style="left:266px">ABOUT US</a>
  <a style="left:413px">SERVICES</a>
  <a style="left:550px">SUPPORT</a>
  <a style="left:690px">CLIENTS</a>
  <a style="left:821px">CAREERS</a>
  <a style="left:954px">CONTACTS</a>
</nav>

<section class="abs hero" role="img" aria-label="Photo of smiling businessmen in suits reviewing a tablet at an office desk"></section>
<div class="abs hero-tag">
  <div class="l1">Let Us Worry About Your Technology...</div>
  <div class="l2">So You Don't Have To!</div>
</div>
<svg class="abs hero-next" width="34" height="64" viewBox="0 0 34 64"><path d="M3 2l28 30L3 62" fill="none" stroke="#fff" stroke-width="2"/></svg>

<h1 class="abs welcome">WELCOME TO <b>KELVANBROOK</b></h1>
<div class="abs divider" style="left:306px;top:779px;width:271px"></div>
<div class="abs divider-mark" style="left:592px;top:771px"></div>
<div class="abs divider" style="left:623px;top:779px;width:271px"></div>
<p class="abs intro">Kelvanbrook Is A Technology Solution Provider Based In Riverton, Texas. Our Goal Is To Make Technology A Non-issue For Individuals And Small To Medium Size Businesses Ranging From 5 To 150 Users.</p>

<div class="abs service-band"></div>
<article class="abs card" style="left:99px"><div class="photo" role="img" aria-label="Photo of hands joining puzzle pieces" style="background:linear-gradient(135deg,#3a3a3a,#c9c2ba 60%,#e9e5e0)"></div><span class="badge"><i></i></span></article>
<article class="abs card" style="left:441px"><div class="photo" role="img" aria-label="Photo of a team meeting around a conference table" style="background:linear-gradient(135deg,#e5e2de,#6d6a69 55%,#2c2c30)"></div><span class="badge"><i></i></span></article>
<article class="abs card" style="left:785px"><div class="photo" role="img" aria-label="Photo of two engineers in a server room" style="background:linear-gradient(135deg,#dfe3e8,#a9b2bd 50%,#5a6270)"></div><span class="badge"><i></i></span></article>
<h3 class="abs service-title" style="left:99px">Managed IT Solutions</h3>
<h3 class="abs service-title" style="left:441px">Remote Diagnostic &amp; Support</h3>
<h3 class="abs service-title" style="left:785px">Infrastructure Design &amp; Installation</h3>
<div class="abs readmore" style="left:186px"><span>READ MORE</span><i></i></div>
<div class="abs readmore" style="left:520px"><span>READ MORE</span><i></i></div>
<div class="abs readmore" style="left:872px"><span>READ MORE</span><i></i></div>

<section class="abs mission"></section>
<section class="abs vision"></section>
<div class="abs mv mission-text"><h2>OUR MISSION</h2><p>Lorem ipsum dolor a sit amet, consectetuer adipiscing elit,the sed diam nonummy nibh euismod tincidunt ut is a laoreet dolore magna aliquam erat volutpat..<em>[+]</em></p></div>
<div class="abs mv vision-text"><h2>OUR VISION</h2><p>Lorem ipsum dolor a sit amet, consectetuer adipiscing elit,the sed diam nonummy nibh euismod tincidunt ut is a laoreet dolore magna aliquam erat volutpat..<em>[+]</em></p></div>
<div class="abs mv-circle"><i></i></div>

<h2 class="abs testi-title">CLIENT <span>TESTIMONIALS</span></h2>
<div class="abs divider" style="left:306px;top:1671px;width:271px"></div>
<div class="abs divider-mark" style="left:592px;top:1663px"></div>
<div class="abs divider" style="left:623px;top:1671px;width:271px"></div>

<div class="abs avatar featured" style="left:215px" role="img" aria-label="Client portrait"></div>
<div class="abs avatar" style="left:557px" role="img" aria-label="Client portrait"></div>
<div class="abs avatar" style="left:901px" role="img" aria-label="Client portrait"></div>
<div class="abs person" style="left:99px"><div class="name">Miss Lena Harwick</div><div class="handle featured">@lharwick</div></div>
<div class="abs person" style="left:441px"><div class="name">Miss Tessa Orlin</div><div class="handle">@torlin</div></div>
<div class="abs person" style="left:785px"><div class="name">Miss Ada Venmore</div><div class="handle">@avenmore</div></div>
<blockquote class="abs quote featured" style="left:99px"><p><b>“</b>Ut wisi enim ad minim veniam, quisl mor nostrni exerci tation ullamcorper suskcipit no lobortis norl nislk ut aliquip.</p><time>4:04PM - FEB 28, 2013</time></blockquote>
<blockquote class="abs quote" style="left:441px"><p><b>“</b>Ut wisi enim ad minim veniam, quisl mor nostrni exerci tation ullamcorper suskcipit no lobortis norl nislk ut aliquip.</p><time>4:04PM - FEB 28, 2013</time></blockquote>
<blockquote class="abs quote" style="left:785px"><p><b>“</b>Ut wisi enim ad minim veniam, quisl mor nostrni exerci tation ullamcorper suskcipit no lobortis norl nislk ut aliquip.</p><time>4:04PM - FEB 28, 2013</time></blockquote>

<svg class="abs footer-curve" width="1200" height="365" viewBox="0 0 1200 365"><path d="M0 110 Q600 -30 1200 110 V365 H0z" fill="#3d3d3f"/></svg>
<div class="abs footer-mark"></div>

<div class="abs fcol links"><h3>Quick <span>Links</span></h3>
  <ul><li>Home</li><li>About Us</li><li>Services</li><li>Support</li><li>Clients</li><li>Careers</li><li>Contact Us</li></ul>
</div>
<div class="abs vsep" style="left:311px;top:2225px"></div>
<div class="abs fcol contact-detail"><h3>Contact <span>Detail</span></h3>
  <p style="margin-top:14px">Kelvanbrook Development Group, Inc.</p>
  <p style="font-size:12.5px;margin-top:4px">1180 Marlow Ave.<br>Riverton, Texas 77099</p>
  <div class="row"><i></i>(555) 014-2290</div>
  <div class="row"><i></i>(555) 014-2290</div>
  <div class="row"><i></i>info@kelvanbrook.com</div>
</div>
<div class="abs vsep" style="left:577px;top:2225px"></div>
<div class="abs fcol quick-contact"><h3>Quick <span>Contact</span></h3>
  <div class="field">Name</div>
  <div class="field">Email</div>
  <div class="field">Message</div>
  <div class="submit">Submit</div>
</div>
<div class="abs vsep" style="left:886px;top:2225px"></div>
<div class="abs footer-brand"><div class="brand"><span class="brand-square"></span>KELVANBROOK</div></div>
<div class="abs social-foot" aria-label="Social links"><span></span><span style="background:#23a6e0"></span><span style="background:#1a79b6"></span></div>

<footer class="abs copybar">Copyright © 2016 Kelvanbrook Development Group, Inc. All Rights Reserved.</footer>

</body>
</html>
```